Business Card Design for company

We want new business cards. We'd like something different-- yet still highly professional. Our tagline is Providing leadership, delivering success. Stock photos are ok, as long as they are relevant and look upscale.

Target Market(s)

Architecture/Business Management Consulting/Engineering Consulting

Contact Information for Business Card

dark gray background with pops of blue might be good, but you tell me. You're the designers. Rounded corners might be nice, but again, you tell me.

Font styles to use
Serif
Sans Serif

Colors
3276b5
5c5c5c
9d9d9d
fbfbfb

Requirements
Nice to have
• Something different, but still very professional.

```html
<!DOCTYPE html>
<html lang="en">
<head>
<meta charset="utf-8">
<title>Corvane Advisory – Business Cards</title>
<link href="https://fonts.googleapis.com/css2?family=Work+Sans:wght@400;500;600&display=swap" rel="stylesheet">
<style>
  :root {
    --page: #262626;
    --card: #333333;
    --card-dark: #2c2c2c;
    --blue: #3276b5;
    --mid-gray: #5c5c5c;
    --light-gray: #9d9d9d;
    --white: #fbfbfb;
    --silver: #c8c8c8;
  }
  * { box-sizing: border-box; margin: 0; padding: 0; }
  html, body { width: 1200px; height: 1198px; overflow: hidden; }
  body {
    background: var(--page);
    font-family: "Work Sans", Arial, sans-serif;
    display: flex;
    align-items: center;
    justify-content: center;
    gap: 38px;
  }
  .card {
    position: relative;
    width: 440px;
    height: 264px;
    border-radius: 12px;
    background: linear-gradient(160deg, var(--card) 0%, var(--card-dark) 100%);
    box-shadow: 0 6px 14px rgba(0,0,0,0.45);
    overflow: hidden;
  }
  .brand-name {
    color: var(--silver);
    font-weight: 500;
    letter-spacing: 0.06em;
    text-transform: uppercase;
    line-height: 1.1;
    display: flex;
    align-items: center;
    gap: 12px;
  }
  .brand-mark {
    width: 12px; height: 12px;
    background: var(--blue);
    flex: none;
  }
  /* Front */
  .card-front { display: flex; flex-direction: column; align-items: center; }
  .card-front .brand-name { margin-top: 84px; font-size: 30px; }
  .tagline {
    position: absolute;
    bottom: 22px; left: 0; right: 0;
    text-align: center;
    font-size: 10px;
    letter-spacing: 0.16em;
    color: var(--light-gray);
    text-transform: uppercase;
  }
  /* Back */
  .card-back .brand-name {
    position: absolute;
    left: 24px; top: 94px;
    font-size: 18px;
    flex-direction: column;
    align-items: flex-start;
    gap: 4px;
  }
  .card-back .brand-name .row { display: flex; align-items: center; gap: 8px; }
  .divider {
    position: absolute;
    left: 210px; top: 74px;
    width: 1px; height: 92px;
    background: var(--blue);
  }
  .contact { position: absolute; left: 228px; top: 78px; }
  .person-name {
    color: var(--blue);
    font-weight: 600;
    font-size: 13px;
    letter-spacing: 0.04em;
    text-transform: uppercase;
  }
  .person-role { color: var(--light-gray); font-size: 9.5px; margin-top: 3px; letter-spacing: 0.03em; }
  .contact-list { list-style: none; margin-top: 14px; }
  .contact-list li {
    display: flex; align-items: center; gap: 7px;
    color: var(--silver);
    font-size: 9.5px;
    line-height: 14px;
  }
  .contact-list svg { width: 7px; height: 7px; flex: none; }
  .address {
    position: absolute; bottom: 30px; left: 0; right: 0;
    text-align: center;
    font-size: 10.5px;
    color: var(--silver);
  }
  .edge-band {
    position: absolute; left: 0; right: 0; bottom: 0; height: 5px;
    background: linear-gradient(90deg, var(--mid-gray), var(--white) 50%, var(--mid-gray));
  }
</style>
</head>
<body>
  <section class="card card-front">
    <div class="brand-name"><span class="brand-mark"></span>Corvane Advisory</div>
    <p class="tagline">Providing Leadership | Delivering Success</p>
  </section>

  <section class="card card-back">
    <div class="brand-name">
      <span class="row"><span class="brand-mark"></span>Corvane</span>
      <span>Advisory</span>
    </div>
    <div class="divider"></div>
    <div class="contact">
      <p class="person-name">Elena Whitcombe</p>
      <p class="person-role">Design Consultant</p>
      <ul class="contact-list">
        <li><svg viewBox="0 0 8 8"><path d="M1 1 L3 1 L3.5 3 L2.5 3.5 Q3.5 5 4.5 5.5 L5 4.5 L7 5 L7 7 Q2 7 1 1Z" fill="#3276b5"/></svg>+1 555-014-2270</li>
        <li><svg viewBox="0 0 8 8"><rect x="0.5" y="1.5" width="7" height="5" fill="#3276b5"/></svg>MARKETING@CORVANEADV.COM</li>
        <li><svg viewBox="0 0 8 8"><rect x="0.5" y="1.5" width="7" height="5" fill="#3276b5"/></svg>INFO@CORVANEADV.COM</li>
        <li><svg viewBox="0 0 8 8"><circle cx="4" cy="4" r="3.5" fill="#3276b5"/></svg>www.corvaneadv.com</li>
      </ul>
    </div>
    <p class="address">418 Harbor Reach Lane Tampa, FL 33602</p>
    <div class="edge-band"></div>
  </section>
</body>
</html>
```